Brightway Carpet and Tile cleaning Business card Design

I need a design that has the same feel as my van.
i would also like a prominent "Review us on facebook" somewhere, but not that it makes it look silly.
I would like the card to have a little bit of grey or black in the design as well.

It will need contact details
phone: 0455 817264
email: rkbrightwayclean@mailbox-example.com
website: www.brightwaycarpetandtilecleaning-example.com.au
facebook: /brightwaycarpetandtilecleaning

Industry/Entity Type

Business

Contact Information for Business Card

Phone number 0455817264
Email rkbrightwayclean@mailbox-example.com
Website www.brightwaycarpetandtilecleaning-example.com.au
Facebook/brightwaycarpetandtilecleaning

Colors
000000

Requirements
Must have
• Same feel as my van
• I want the card to stand out from the crowd
Nice to have
• Maybe include a tiny bit of a third colour? Grey's,blacks, orange?

```html
<!DOCTYPE html>
<html lang="en">
<head>
<meta charset="utf-8">
<title>Brightway Carpet and Tile cleaning – Business Card</title>
<link href="https://fonts.googleapis.com/css2?family=Open+Sans:wght@400;600;700&display=swap" rel="stylesheet">
<style>
  :root {
    --backdrop-top: #2a2a2a;
    --backdrop-bottom: #050505;
    --card-white: #ffffff;
    --sky-top: #a2e4f4;
    --sky-bottom: #03acdb;
    --brand-blue: #1a9fd2;
    --brand-deep: #0f6f94;
    --text-grey: #555a5e;
    --white: #ffffff;
  }
  * { margin: 0; padding: 0; box-sizing: border-box; }
  html, body {
    width: 1200px;
    height: 900px;
    overflow: hidden;
  }
  body {
    position: relative;
    background: linear-gradient(180deg, var(--backdrop-top) 0%, #161616 55%, var(--backdrop-bottom) 100%);
    font-family: "Open Sans", Arial, sans-serif;
  }
  .card {
    position: absolute;
    top: 306px;
    width: 440px;
    height: 271px;
    border-radius: 12px;
    box-shadow: 0 2px 6px rgba(0,0,0,0.5);
    display: flex;
    flex-direction: column;
    align-items: center;
  }
  .card--front {
    left: 149px;
    background: var(--card-white);
  }
  .card--back {
    left: 608px;
    width: 441px;
    background: linear-gradient(180deg, var(--sky-top) 0%, var(--sky-bottom) 100%);
  }
  .brand-name {
    display: flex;
    align-items: center;
    gap: 10px;
    font-weight: 700;
    color: var(--brand-blue);
    text-align: left;
    line-height: 1;
  }
  .brand-name__dot {
    width: 26px;
    height: 26px;
    border-radius: 50%;
    background: var(--brand-blue);
    flex: none;
  }
  .brand-name__text { display: flex; flex-direction: column; }
  .brand-name__main { font-size: 42px; letter-spacing: -0.5px; }
  .brand-name__sub { font-size: 14px; letter-spacing: 1.5px; margin-top: 4px; }
  .card--front .brand-name { margin-top: 64px; }
  .card--back .brand-name { margin-top: 90px; color: var(--brand-deep); }
  .card--back .brand-name__dot { background: var(--brand-deep); }

  .contact-list {
    list-style: none;
    margin-top: 42px;
    font-size: 12.5px;
    color: var(--text-grey);
    text-align: center;
  }
  .contact-list li {
    height: 18px;
    display: flex;
    align-items: center;
    justify-content: center;
    gap: 5px;
  }
  .contact-icon { width: 10px; height: 10px; flex: none; fill: var(--brand-blue); }
  .contact-list--long li { font-size: 12px; }

  .promo-line {
    margin-top: 46px;
    font-size: 13px;
    font-weight: 700;
    color: var(--white);
  }
</style>
</head>
<body>
  <section class="card card--front" aria-label="Business card front">
    <div class="brand-name">
      <span class="brand-name__dot"></span>
      <span class="brand-name__text">
        <span class="brand-name__main">Brightway</span>
        <span class="brand-name__sub">CARPET &amp; TILE CLEANING</span>
      </span>
    </div>
    <ul class="contact-list contact-list--long">
      <li>
        <svg class="contact-icon" viewBox="0 0 10 10" aria-hidden="true"><path d="M2 0.5 L3.6 2.6 L2.7 3.6 C3.3 5 5 6.7 6.4 7.3 L7.4 6.4 L9.5 8 L8.3 9.5 C4.5 9.2 0.8 5.5 0.5 1.7 Z"/></svg>
        0455 817264
      </li>
      <li>
        <svg class="contact-icon" viewBox="0 0 10 10" aria-hidden="true"><path d="M0.5 2 H9.5 V8 H0.5 Z M1 2.4 L5 5.3 L9 2.4" stroke="#fff" stroke-width="0.8"/></svg>
        rkbrightwayclean@mailbox-example.com
      </li>
      <li>
        <svg class="contact-icon" viewBox="0 0 10 10" aria-hidden="true"><circle cx="5" cy="5" r="4.5"/><path d="M0.5 5 H9.5 M5 0.5 C2.8 3 2.8 7 5 9.5 M5 0.5 C7.2 3 7.2 7 5 9.5" stroke="#fff" stroke-width="0.7" fill="none"/></svg>
        www.brightwaycarpetandtilecleaning-example.com.au
      </li>
      <li>
        <svg class="contact-icon" viewBox="0 0 10 10" aria-hidden="true"><rect x="0.5" y="0.5" width="9" height="9" rx="1.5"/></svg>
        /brightwaycarpetandtilecleaning
      </li>
    </ul>
  </section>

  <section class="card card--back" aria-label="Business card back">
    <div class="brand-name">
      <span class="brand-name__dot"></span>
      <span class="brand-name__text">
        <span class="brand-name__main">Brightway</span>
        <span class="brand-name__sub">CARPET &amp; TILE CLEANING</span>
      </span>
    </div>
    <p class="promo-line">Win Carpet Cleaning For YOU and a FRIEND!</p>
  </section>
</body>
</html>
```